Software allocation system needs a business card design

We need a business card designed for our software platform - www.tallivo.com.au

At the moment the logo and website is all black and white, we are happy for suggestions on implementing some colour throughout either the logo or business card.

Industry/Entity Type

Software

Font styles to use
Sans Serif

Colors

Designer to choose colors to be used in the design.

```html
<!DOCTYPE html>
<html lang="en">
<head>
<meta charset="utf-8">
<title>Tallivo Business Card</title>
<link rel="stylesheet" href="https://fonts.googleapis.com/css2?family=Lato:wght@300;400&family=Montserrat:wght@400;700&family=PT+Sans+Narrow&display=swap">
<style>
  :root {
    --paper: #f2f2f2;
    --ink: #1c1c1c;
    --ink-soft: #3a3a3a;
    --sky: #5bbfea;
    --rule: #9a9a9a;
    --band-grey: #c4c4c4;
  }
  html, body {
    margin: 0;
    padding: 0;
    overflow: hidden;
    background: #ffffff;
  }
  .card {
    position: relative;
    width: 1200px;
    height: 685px;
    background: var(--paper);
    overflow: hidden;
    font-family: "Lato", sans-serif;
    color: var(--ink);
  }
  .top-bar {
    position: absolute;
    left: 213px;
    top: 0;
    width: 780px;
    height: 8px;
    background: var(--sky);
    border-radius: 0 0 8px 8px;
  }
  .brand-name {
    position: absolute;
    left: 0;
    right: 0;
    top: 122px;
    text-align: center;
    font-family: "Lato", sans-serif;
    font-weight: 300;
    font-size: 78px;
    letter-spacing: 10px;
    line-height: 1;
    color: var(--ink);
  }
  .tagline {
    position: absolute;
    left: 0;
    right: 0;
    top: 246px;
    text-align: center;
    font-family: "PT Sans Narrow", sans-serif;
    font-size: 37px;
    line-height: 1;
    color: var(--ink-soft);
    letter-spacing: -0.3px;
  }
  .divider {
    position: absolute;
    left: 602px;
    top: 367px;
    width: 2px;
    height: 250px;
    background: var(--rule);
  }
  .contact-list {
    position: absolute;
    left: 92px;
    margin: 0;
    padding: 0;
    list-style: none;
    font-size: 22px;
    line-height: 1.35;
  }
  .contact-list li {
    position: relative;
    padding-left: 47px;
  }
  .contact-list .icon {
    position: absolute;
    left: 0;
    top: 3px;
    width: 28px;
    height: 28px;
    fill: var(--ink-soft);
  }
  .address { top: 387px; }
  .phones { top: 470px; }
  .phones li { height: 34px; }
  .person {
    position: absolute;
    left: 607px;
    right: 0;
    top: 374px;
    text-align: center;
    font-family: "Montserrat", sans-serif;
  }
  .person-name {
    margin: 0;
    font-weight: 700;
    font-size: 35px;
    line-height: 1.1;
    color: var(--ink);
  }
  .person-name .surname { color: var(--sky); }
  .person-role {
    margin: 0;
    font-weight: 400;
    font-size: 29px;
    line-height: 1.05;
    color: var(--ink);
  }
  .online {
    position: absolute;
    left: 768px;
    top: 506px;
    margin: 0;
    padding: 0;
    list-style: none;
    font-size: 21px;
  }
  .online li {
    position: relative;
    padding-left: 47px;
    height: 35px;
  }
  .online .icon {
    position: absolute;
    left: 0;
    top: 2px;
    width: 30px;
    height: 26px;
    fill: none;
    stroke: var(--ink-soft);
    stroke-width: 2;
  }
  .bottom-bands {
    position: absolute;
    left: 0;
    bottom: 0;
    width: 1200px;
    height: 40px;
  }
</style>
</head>
<body>
<div class="card">
  <div class="top-bar"></div>

  <div class="brand-name">TALLIVO</div>
  <div class="tagline">PLANNING &amp; COMPLIANCE FOR HEAVY INDUSTRY</div>

  <ul class="contact-list address">
    <li>
      <svg class="icon" viewBox="0 0 24 24" aria-hidden="true"><path d="M12 1C7.6 1 4.5 4.3 4.5 8.4 4.5 14 12 23 12 23s7.5-9 7.5-14.6C19.5 4.3 16.4 1 12 1zm0 10.4a3 3 0 1 1 0-6 3 3 0 0 1 0 6z"/></svg>
      PO Box 712<br>Ryde Park NSW 2112
    </li>
  </ul>

  <ul class="contact-list phones">
    <li>
      <svg class="icon" viewBox="0 0 24 24" aria-hidden="true"><path d="M2 9c0-3 4-5 10-5s10 2 10 5v2h-5V8.5c-1.5-.6-3.2-.9-5-.9s-3.5.3-5 .9V11H2zM6 12l2.5-3h7L18 12l2 8H4z"/></svg>
      555 214 3080
    </li>
    <li>
      <svg class="icon" viewBox="0 0 24 24" aria-hidden="true"><path d="M7 2h8l3 3v5H7zM3 10h2v11H3zM6 11h15v10H6zm3 3v2h2v-2zm4 0v2h2v-2zm4 0v2h2v-2zm-8 4v1h10v-1z"/></svg>
      555 214 3091
    </li>
    <li>
      <svg class="icon" viewBox="0 0 24 24" aria-hidden="true"><path d="M7 1h10a1.5 1.5 0 0 1 1.5 1.5v19A1.5 1.5 0 0 1 17 23H7a1.5 1.5 0 0 1-1.5-1.5v-19A1.5 1.5 0 0 1 7 1zm1 3v14h8V4zm4 15.5a1.2 1.2 0 1 0 0 2.4 1.2 1.2 0 0 0 0-2.4z"/></svg>
      555 7720 4416
    </li>
  </ul>

  <div class="divider"></div>

  <div class="person">
    <p class="person-name">Sam <span class="surname">Carter</span></p>
    <p class="person-role">Job title here</p>
  </div>

  <ul class="online">
    <li>
      <svg class="icon" viewBox="0 0 30 26" aria-hidden="true"><rect x="2" y="4" width="26" height="18"/><path d="M2 4l13 10L28 4M2 22l10-9M28 22l-10-9"/></svg>
      hello@tallivo.com.au
    </li>
    <li>
      <svg class="icon" viewBox="0 0 30 26" aria-hidden="true"><rect x="5" y="3" width="20" height="14"/><path d="M1 21h28v2H1z"/></svg>
      www.tallivo.com.au
    </li>
  </ul>

  <svg class="bottom-bands" viewBox="0 0 1200 40" aria-hidden="true">
    <polygon points="0,22 770,22 760,40 0,40" fill="var(--band-grey)"/>
    <path d="M790 40 L790 26 Q790 8 812 8 L1200 8 L1200 40 Z" fill="var(--sky)"/>
  </svg>
</div>
</body>
</html>
```